Business Card Design for Occupational Medicine Start Up Company

We need to design a professional business card. We are a healthcare company providing occupational medicine services to blue collar industries. We are professional, efficient and high quality service providers.

Target Market(s)

Blue Collar Industry: Shipbuilding, Ports, Trucking Companies; The Executives and Safety Officers for these companies

Industry/Entity Type

Healthcare

Contact Information for Business Card

Logo, Name, Title, Email, Phone

Other font styles liked:
• Please match our Brand Guide

Requirements
Must have
• Our Company Colors and Logo

```html
<!DOCTYPE html>
<html lang="en">
<head>
<meta charset="utf-8">
<title>CrewCare Business Card</title>
<link rel="stylesheet" href="https://fonts.googleapis.com/css2?family=Montserrat:wght@400;700;800&family=Roboto:wght@400&display=swap">
<style>
  :root {
    --navy: #2a3589;
    --navy-deep: #232c78;
    --sky: #22a7de;
    --amber: #f2ae45;
    --white: #ffffff;
    --ink: #1f2a6e;
    --stage: #e9ebf0;
  }
  * { margin: 0; padding: 0; box-sizing: border-box; }
  html, body { width: 1200px; height: 912px; overflow: hidden; background: var(--stage); }
  .stage {
    width: 1200px; height: 912px;
    display: flex; flex-direction: column; align-items: center; justify-content: center; gap: 40px;
  }
  .card {
    position: relative; width: 720px; height: 412px; overflow: hidden;
    box-shadow: 0 10px 30px rgba(20, 30, 70, 0.25);
  }
  /* Back side */
  .card-back { background: var(--navy); }
  .back-pattern {
    position: absolute; inset: 0;
    background: radial-gradient(circle at 60% 40%, #3140a0 0%, var(--navy) 55%, var(--navy-deep) 100%);
  }
  .back-brand {
    position: absolute; right: 92px; top: 196px;
    font-family: "Montserrat", sans-serif; font-weight: 800; font-size: 16px;
    color: var(--white); letter-spacing: 1px;
  }
  /* Front side */
  .card-front { background: var(--white); }
  .waves { position: absolute; inset: 0; }
  .brand {
    position: absolute; left: 72px; top: 190px;
    display: flex; align-items: center; gap: 12px;
  }
  .brand-dot { width: 22px; height: 22px; border-radius: 50%; background: var(--navy); }
  .brand-name {
    font-family: "Montserrat", sans-serif; font-weight: 800; font-size: 40px;
    color: var(--navy); letter-spacing: 1px;
  }
  .person { position: absolute; right: 96px; top: 42px; text-align: right; }
  .person-name {
    font-family: "Montserrat", sans-serif; font-weight: 800; font-size: 26px;
    color: var(--navy); letter-spacing: -0.3px;
  }
  .person-title {
    font-family: "Roboto", sans-serif; font-size: 14px; color: #222; margin-top: 2px;
  }
  .corner-square {
    position: absolute; right: 48px; top: 38px; width: 30px; height: 30px; background: var(--navy);
  }
  .contact {
    position: absolute; right: 40px; top: 250px; list-style: none; text-align: right;
    font-family: "Roboto", sans-serif; font-size: 16px; color: var(--white); line-height: 24px;
  }
  .contact li { display: flex; align-items: center; justify-content: flex-end; gap: 8px; }
  .contact svg { width: 12px; height: 12px; flex: none; }
</style>
</head>
<body>
<main class="stage">
  <section class="card card-back" aria-label="Card back">
    <div class="back-pattern" role="img" aria-label="Tonal navy pattern of repeated brand marks"></div>
    <span class="back-brand">CREWCARE</span>
  </section>

  <section class="card card-front" aria-label="Card front">
    <svg class="waves" viewBox="0 0 720 412" aria-hidden="true">
      <path d="M0 372 C 260 392, 400 340, 480 240 C 540 165, 600 140, 720 138 L720 412 L0 412 Z" fill="var(--navy)"/>
      <path d="M0 360 C 250 380, 385 330, 465 232 C 525 158, 590 128, 690 118" fill="none" stroke="var(--sky)" stroke-width="10"/>
      <path d="M0 344 C 230 362, 355 318, 430 230 C 450 205, 460 190, 470 178" fill="none" stroke="var(--amber)" stroke-width="10"/>
    </svg>

    <div class="brand">
      <span class="brand-dot"></span>
      <span class="brand-name">CREWCARE</span>
    </div>

    <div class="person">
      <p class="person-name">DANIEL HAYES</p>
      <p class="person-title">Director</p>
    </div>
    <span class="corner-square"></span>

    <ul class="contact">
      <li>(480) 555 0142
        <svg viewBox="0 0 12 12"><path d="M2 1 L4.5 1 L5.5 3.5 L4 4.5 C4.7 6 6 7.3 7.5 8 L8.5 6.5 L11 7.5 L11 10 C6 10.5 1.5 6 2 1 Z" fill="var(--amber)"/></svg>
      </li>
      <li>info@crewcaremed.com
        <svg viewBox="0 0 12 12"><rect x="0.5" y="2" width="11" height="8" fill="var(--amber)"/><path d="M0.5 2 L6 6.5 L11.5 2" fill="none" stroke="var(--navy)" stroke-width="1"/></svg>
      </li>
      <li>www.crewcaremed.com
        <svg viewBox="0 0 12 12"><circle cx="6" cy="6" r="5.5" fill="var(--amber)"/><path d="M0.5 6 H11.5 M6 0.5 V11.5" stroke="var(--navy)" stroke-width="0.8"/><ellipse cx="6" cy="6" rx="2.4" ry="5.5" fill="none" stroke="var(--navy)" stroke-width="0.8"/></svg>
      </li>
    </ul>
  </section>
</main>
</body>
</html>
```